Webpages for Vuolahtinen Software Consulting

Needed: Webpage design.
Details:
One page site with good looking fonts and simple modern design. Logo would also be nice.
Page is for Software consulting company called: "Vuolahtinen Software Consulting". Vuolahtinen is my surname.
Pages should tell viewer that the company is reliable and its employees are hard-core professionals.
Company currently has one employee, that's me. So what I do is what this company does. I am software consultant. Basicly that means that I do Java/JavaEE/Web programming as subcontractor.
Here is more detail information about me.
SPECIALTIES
- Enterprise J2EE Application Programming and Architectures,
- Web development and
- Agile development.
I have over a decade of experience on designing and creating Java based web-services and applications to multiple interfaces. I also have plenty of experience about software architectures, design patterns and integration into third party systems. I’ve got good knowledge about agile software development and testing processes and I am experienced ScrumMaster and software project leader.
Target Market(s)
IT Businesses, Coding companies... Anyone who is buying coding as service.
Industry/Entity Type
Software
Look and feel

```html
<!DOCTYPE html>
<html lang="en">
<head>
<meta charset="utf-8">
<title>Vuolahtinen Software Consulting</title>
<link rel="stylesheet" href="https://fonts.googleapis.com/css2?family=Oswald:wght@400&family=PT+Serif:wght@400&family=Arimo:wght@400;700&display=swap">
<style>
:root{
  --ink:#3a3a3a;
  --muted:#6d6d6d;
  --green:#2ea12e;
  --green-dark:#1d7d1d;
  --teal:#2a8fb5;
  --hero-top:#f1f1f1;
  --hero-bottom:#dcdcdc;
  --line:#d9d9d9;
  --footer:#262626;
  --footer-line:#3c3c3c;
  --footer-text:#9a9a9a;
}
*{margin:0;padding:0;box-sizing:border-box}
html,body{width:736px;height:1200px;overflow:hidden;background:#fff}
body{position:relative;font-family:"Arimo",Arial,sans-serif;color:var(--ink)}
.abs{position:absolute}

.hero{left:0;top:0;width:736px;height:395px;background:linear-gradient(180deg,var(--hero-top),var(--hero-bottom))}
.brand{left:61px;top:34px;font-size:23px;color:#2b2b2b;display:flex;align-items:center;gap:8px}
.brand-mark{width:14px;height:14px;background:var(--green)}
.top-nav{right:60px;top:58px;font-size:11px;color:var(--muted)}
.top-nav a{color:var(--muted);text-decoration:none;margin:0 6px}
.top-nav .current{color:var(--green)}
.social{top:16px;width:16px;height:16px;border-radius:50%;background:#a9a9a9}
.headline{left:147px;top:98px;font-family:"Oswald",sans-serif;font-weight:400;font-size:28px;color:#4a4a4a;letter-spacing:.2px}
.specialties-title{left:61px;top:166px;font-family:"PT Serif",serif;font-weight:400;font-size:18px;color:var(--teal);letter-spacing:1px}
.specialties{left:61px;top:200px;width:372px;list-style:none;font-family:"PT Serif",serif;font-size:13px;color:#333}
.specialties li{display:flex;align-items:center;gap:9px;height:32px;white-space:nowrap}
.specialties .dot{width:18px;height:18px;border-radius:50%;background:#8fb8d0;flex:none}
.cta{left:147px;top:322px;width:136px;height:40px;border-radius:4px;background:linear-gradient(var(--green),var(--green-dark));color:#fff;font-size:16px;font-weight:700;display:flex;align-items:center;justify-content:center}
.hero-art{left:448px;top:155px;width:260px;height:220px;border-radius:6px;background:linear-gradient(160deg,#6f9fd0,#2c3b55 70%,#1a1f2b)}

.skills{left:0;top:395px;width:736px;height:108px;border-bottom:1px solid var(--line);background:#f7f7f7}
.skill{top:32px;display:flex;align-items:center;gap:10px}
.skill-num{width:44px;height:44px;border-radius:50%;background:#2f2f2f;color:#fff;font-family:"PT Serif",serif;font-size:18px;display:flex;align-items:center;justify-content:center}
.skill-name{font-family:"PT Serif",serif;font-size:19px;line-height:1;color:#333}
.skill-name small{display:block;font-size:12px;letter-spacing:1px;color:var(--muted);margin-top:3px}

.section-title{font-family:"PT Serif",serif;font-weight:400;font-size:16px;letter-spacing:1px;color:#444}
.rule{height:1px;background:var(--line)}
.service{left:61px;width:380px;display:flex;gap:22px}
.service-icon{width:50px;height:50px;border-radius:8px;flex:none}
.item-title{font-size:9px;font-weight:700;color:var(--green);margin-bottom:6px}
.item-text{font-size:9px;line-height:1.55;color:var(--muted)}
.small-btn{height:18px;padding:0 8px;border-radius:3px;background:var(--green);color:#fff;font-size:8px;display:flex;align-items:center}
.see-all{font-size:9px;color:var(--green);text-decoration:underline}
.avatar{width:22px;height:22px;border-radius:50%;background:#b8b8b8}

.footer{left:0;top:915px;width:736px;height:285px;background:var(--footer)}
.touch-title{left:61px;top:931px;font-size:16px;font-weight:700;color:var(--teal);letter-spacing:1px}
.field{left:61px;width:185px;height:20px;background:#efefef;border-radius:2px;font-size:9px;color:#777;padding:5px 8px}
.comments{left:258px;top:962px;width:417px;height:58px;background:#efefef;border-radius:2px;font-size:9px;color:#777;padding:6px 8px}
.form-btn{top:1034px;height:18px;padding:0 10px;border-radius:2px;background:var(--green);color:#fff;font-size:9px;display:flex;align-items:center}
.foot-line{left:61px;top:1072px;width:614px;height:1px;background:var(--footer-line)}
.foot-nav{left:0;width:736px;top:1094px;text-align:center;font-size:10px;color:#ccc}
.foot-text{left:0;width:736px;text-align:center;font-size:9px;color:var(--footer-text)}
.follow{left:0;width:736px;top:1162px;display:flex;justify-content:center;align-items:center;gap:6px;font-size:9px;color:var(--footer-text)}
.follow span.sq{width:13px;height:13px;background:#666;border-radius:2px}
</style>
</head>
<body>

<section class="hero abs"></section>
<div class="hero-art abs" role="img" aria-label="Tablet showing a rising bar chart with an arrow"></div>
<div class="brand abs"><span class="brand-mark"></span>Vuolahtinen Software Consulting</div>
<span class="social abs" style="left:650px"></span>
<span class="social abs" style="left:674px"></span>
<nav class="top-nav abs"><a class="current">Home</a>|<a>Contact Us</a></nav>

<h1 class="headline abs">We are reliable and hard-core professionals.</h1>
<h2 class="specialties-title abs">SPECIALTIES</h2>
<ul class="specialties abs">
  <li><span class="dot"></span>Enterprise J2EE Application Programming and Architectures,</li>
  <li><span class="dot"></span>Web development</li>
  <li><span class="dot"></span>Agile development.</li>
</ul>
<div class="cta abs">Learn More</div>

<section class="skills abs">
  <div class="skill abs" style="left:61px"><span class="skill-num">01</span><span class="skill-name">JAVA<small>PROGRAMMING</small></span></div>
  <div class="skill abs" style="left:294px"><span class="skill-num">02</span><span class="skill-name">JAVAEE<small>PROGRAMMING</small></span></div>
  <div class="skill abs" style="left:522px"><span class="skill-num">03</span><span class="skill-name">WEB<small>PROGRAMMING</small></span></div>
</section>

<h3 class="section-title abs" style="left:61px;top:540px">OUR SERVICES</h3>
<div class="rule abs" style="left:61px;top:566px;width:380px"></div>

<div class="service abs" style="top:589px">
  <div class="service-icon" role="img" aria-label="Application window icon" style="background:linear-gradient(#9ec6ea,#3d7fc0)"></div>
  <div><p class="item-title">LOREM IPSUM DOLOR SIT AMET CONSE</p>
  <p class="item-text">Lorem ipsum dolor sit amet conse ctetur adipisicing elit, sed do eiusmod tempor incididunt ut labore et dolore magna aliqua. Ut enim ad minim veniam quis nostrud exercitation ullamco laboris nisi ut aliquip. »</p></div>
</div>
<div class="service abs" style="top:687px">
  <div class="service-icon" role="img" aria-label="Document folders icon" style="background:linear-gradient(#f3dd9b,#c79b3e)"></div>
  <div><p class="item-title">LOREM IPSUM DOLOR SIT AMET CONSE</p>
  <p class="item-text">Lorem ipsum dolor sit amet conse ctetur adipisicing elit, sed do eiusmod tempor incididunt ut labore et dolore magna aliqua. Ut enim ad minim veniam quis nostrud exercitation ullamco laboris nisi ut aliquip. »</p></div>
</div>
<div class="service abs" style="top:785px">
  <div class="service-icon" role="img" aria-label="Gear settings icon" style="background:radial-gradient(#9ee06a,#3f9b1e);border-radius:50%"></div>
  <div><p class="item-title">LOREM IPSUM DOLOR SIT AMET CONSE</p>
  <p class="item-text">Lorem ipsum dolor sit amet conse ctetur adipisicing elit, sed do eiusmod tempor incididunt ut labore et dolore magna aliqua. Ut enim ad minim veniam quis nostrud exercitation ullamco laboris nisi ut aliquip. »</p></div>
</div>
<div class="rule abs" style="left:61px;top:850px;width:380px"></div>
<div class="small-btn abs" style="left:61px;top:858px">See all services</div>

<h3 class="section-title abs" style="left:466px;top:540px">ABOUT US</h3>
<div class="rule abs" style="left:466px;top:566px;width:209px"></div>
<div class="abs" style="left:466px;top:589px;width:209px">
  <p class="item-title">LOREM IPSUM DOLOR SIT AMET CONSE CTETUR ADIPISICING ELIT</p>
  <p class="item-text">Lorem ipsum dolor sit amet conse ctetur adipisicing elit, sed do tempor incididunt ut labore et dolore magna aliqua. Ut enim ad minim veniam, quis nostrud exercitation ullamco laboris nisi ut aliquip. »</p>
</div>
<h3 class="section-title abs" style="left:466px;top:716px">TESTIMONIALS</h3>
<div class="rule abs" style="left:466px;top:740px;width:209px"></div>
<p class="item-text abs" style="left:466px;top:750px;width:209px">Lorem ipsum dolor sit amet conse ctetur adipisicing elit, sed do tempor incididunt ut labore et dolore magna aliqua. »</p>
<div class="abs" style="left:556px;top:815px;display:flex;gap:6px;align-items:center">
  <span class="avatar" role="img" aria-label="Client portrait"></span>
  <span class="item-text" style="line-height:1.3">Lorem ipsum dolor<br>Sit amet conse</span>
</div>
<div class="rule abs" style="left:466px;top:850px;width:209px"></div>
<a class="see-all abs" style="left:466px;top:862px">See all</a>

<footer class="footer abs"></footer>
<h3 class="touch-title abs">GET IN TOUCH</h3>
<div class="field abs" style="top:962px">Name</div>
<div class="field abs" style="top:996px">E-mail</div>
<div class="form-btn abs" style="left:61px">Send</div>
<div class="form-btn abs" style="left:103px">Reset</div>
<div class="comments abs">Comments</div>
<div class="foot-line abs"></div>
<p class="foot-nav abs">Home &nbsp;|&nbsp; Contact Us</p>
<p class="foot-text abs" style="top:1120px">© Copyright 2012 Vuolahtinen Software Consulting. All Rights Reserved</p>
<p class="foot-text abs" style="top:1136px">Website Design &amp; Developed | Pixelhaven Studio | www.vuolahtinen-consulting.example</p>
<div class="follow abs">Follow Us : <span class="sq"></span><span class="sq"></span></div>

</body>
</html>
```